business card deign

Logo needs the following on it.
1. attached logo
2. Tagline - "From the first chill to the last toast...we bring it!"
3. Name- Dalton Pikes, Founder and CPO
4. Address - 412 E. Carver Avenue, Ste 2207, Tampa, FL. 33917
5. Phone - 555.318.4726

```html
<!DOCTYPE html>
<html lang="en">
<head>
<meta charset="UTF-8">
<title>Hopley Business Card</title>
<link href="https://fonts.googleapis.com/css2?family=Montserrat:wght@300;400;700&display=swap" rel="stylesheet">
<style>
  :root {
    --ink: #000000;
    --paper: #ffffff;
    --backdrop: #c9c6c8;
    --text-dark: #1a1a1a;
    --text-muted: #2b2b2b;
  }
  * { margin: 0; padding: 0; box-sizing: border-box; }
  html, body {
    width: 1200px;
    height: 800px;
    overflow: hidden;
    background: var(--backdrop);
    font-family: "Montserrat", sans-serif;
  }
  .stage {
    position: relative;
    width: 1200px;
    height: 800px;
    display: flex;
    align-items: center;
    justify-content: center;
    gap: 40px;
  }
  .card {
    width: 540px;
    height: 310px;
    border-radius: 18px;
    overflow: hidden;
    box-shadow: 0 10px 30px rgba(0,0,0,0.25);
    position: relative;
  }
  .card-front {
    background: var(--ink);
    display: flex;
    flex-direction: column;
    align-items: center;
    justify-content: center;
  }
  .wordmark {
    color: var(--paper);
    font-weight: 700;
    letter-spacing: 0.42em;
    font-size: 40px;
    padding-left: 0.42em;
    white-space: nowrap;
  }
  .card-front .wordmark { margin-top: 20px; }
  .tagline {
    color: var(--paper);
    font-weight: 300;
    font-size: 13.5px;
    letter-spacing: 0.02em;
    margin-top: 38px;
    white-space: nowrap;
  }
  .card-back { display: flex; }
  .brand-panel {
    width: 46%;
    background: var(--ink);
    display: flex;
    align-items: center;
    justify-content: center;
  }
  .brand-panel .wordmark { font-size: 30px; }
  .contact-panel {
    flex: 1;
    background: var(--paper);
    padding: 58px 0 0 34px;
    color: var(--text-dark);
  }
  .person-name {
    font-weight: 700;
    font-size: 22px;
    line-height: 1.1;
  }
  .person-title {
    font-weight: 400;
    font-size: 12.5px;
    margin-top: 3px;
    color: var(--text-muted);
  }
  .address {
    font-weight: 300;
    font-size: 12.5px;
    line-height: 1.35;
    margin-top: 22px;
  }
  .contact-list {
    list-style: none;
    margin-top: 14px;
  }
  .contact-list li {
    display: flex;
    align-items: center;
    gap: 10px;
    font-weight: 300;
    font-size: 12.5px;
    line-height: 1;
    margin-bottom: 10px;
  }
  .contact-icon {
    width: 13px;
    height: 13px;
    flex: none;
  }
</style>
</head>
<body>
<main class="stage">
  <section class="card card-front">
    <div class="wordmark">HOPLEY</div>
    <p class="tagline">From the first chill to the last toast...we bring it</p>
  </section>

  <section class="card card-back">
    <div class="brand-panel">
      <div class="wordmark">HOPLEY</div>
    </div>
    <div class="contact-panel">
      <h1 class="person-name">Dalton Pikes</h1>
      <p class="person-title">Founder and CPO</p>
      <p class="address">412 E. Carver Avenue, Ste 2207,<br>Tampa, FL. 33917</p>
      <ul class="contact-list">
        <li>
          <svg class="contact-icon" viewBox="0 0 16 16" aria-hidden="true">
            <circle cx="8" cy="8" r="8" fill="var(--ink)"/>
            <path d="M5.2 4.2l1.6-.4.8 2-1 .8a5 5 0 0 0 2.8 2.8l.8-1 2 .8-.4 1.6c-3.6.2-6.8-3-6.6-6.6z" fill="var(--paper)"/>
          </svg>
          555.318.4726
        </li>
        <li>
          <svg class="contact-icon" viewBox="0 0 16 16" aria-hidden="true">
            <rect x="1" y="3" width="14" height="10" rx="1.5" fill="var(--ink)"/>
            <path d="M2 4.5l6 4.2 6-4.2" fill="none" stroke="var(--paper)" stroke-width="1.2"/>
          </svg>
          info@hopley.com
        </li>
        <li>
          <svg class="contact-icon" viewBox="0 0 16 16" aria-hidden="true">
            <circle cx="8" cy="8" r="8" fill="var(--ink)"/>
            <ellipse cx="8" cy="8" rx="3" ry="6.5" fill="none" stroke="var(--paper)" stroke-width="1"/>
            <path d="M1.5 8h13M2.5 5h11M2.5 11h11" stroke="var(--paper)" stroke-width="1"/>
          </svg>
          www.hopley.com
        </li>
      </ul>
    </div>
  </section>
</main>
</body>
</html>
```